A new updated business card. A good first impression for new customers to our business.

I need something unique. I will attached a picture of our old rubbish cards, and also our current Logo ( I think this needs an update if you have any ideas, its very basic and budget)The best way you will get to see my business is checking our Facebook page, I don't really know what else to say, but anything you want to know, ask away.www.facebook.com/tkwashandseal/

Target Market(s)

Home owners

Industry/Entity Type

Business

Contact Information for Business Card

T&K's Pressure Cleaning & Concrete Sealing
Maya 0492 615 370 maya@tkwashandseal.com
Dylan 0431 528 906 dylan@tkwashandseal.com

FB: www.facebook.com/tkwashandseal/
Website: www.tkwashandseal.net (This is pretty rubbish- we don't really use it)

100% customer satisfaction guaranteed

All aspects of Hi-Pressure Cleaning
Sealing & Re-Sealing
Roof Cleaning
Colour sealing
Decorative coatings

Free no obligation quotes

Requirements
Must have
• NO OBLIGATION FREE quotes
• 100% Customer satisfaction guaranteed
• Can you please add both names, contact details and email address on one card.
• Dylan 0431 528 906
• dylan@tkwashandseal.com
• Maya 0492 615 370
• maya@tkwashandseal.com
• Please change the services:
• Hot/Cold Hi-Pressure Cleaning
• Sealing & Re-Sealing
• Roof Cleaning
• Colour Sealing
• Decorative Coatings
• Concrete Honing
• Thanks
Nice to have
• Something a bit different, something eye catching.l

```html
<!DOCTYPE html>
<html lang="en">
<head>
<meta charset="utf-8">
<title>T&amp;K's Pressure Cleaning &amp; Concrete Sealing – Business Card</title>
<link rel="stylesheet" href="https://fonts.googleapis.com/css2?family=Open+Sans:wght@400;600;700&display=swap">
<style>
  :root {
    --backdrop: #3b3430;
    --card: #ffffff;
    --red: #e0201f;
    --ink: #2b2b2b;
    --grey: #5a5a5a;
    --rule: #dcdcdc;
    --badge-blue: #1f78c8;
    --badge-gold: #e8b92e;
  }
  * { box-sizing: border-box; margin: 0; padding: 0; }
  html, body { width: 1200px; height: 844px; overflow: hidden; }
  body {
    background: var(--backdrop);
    font-family: "Open Sans", Arial, sans-serif;
    color: var(--ink);
    display: flex;
    align-items: center;
    justify-content: center;
    gap: 40px;
  }
  .card {
    width: 540px;
    height: 310px;
    background: var(--card);
    box-shadow: 0 10px 24px rgba(0,0,0,.45);
    position: relative;
  }

  /* Contact side */
  .card--contact { display: flex; }
  .brand-panel {
    width: 47%;
    display: flex;
    align-items: center;
    justify-content: center;
    padding: 40px 22px 0;
  }
  .divider { width: 1px; background: var(--rule); margin: 28px 0; }
  .contact-panel {
    flex: 1;
    padding: 26px 22px 0 22px;
    font-size: 13px;
  }
  .person-name {
    color: var(--red);
    font-weight: 700;
    font-size: 17px;
    line-height: 1.2;
  }
  .person + .person { margin-top: 12px; }
  .contact-line {
    display: flex;
    align-items: center;
    gap: 9px;
    line-height: 1.65;
  }
  .contact-line svg { flex: none; }
  .social { margin-top: 14px; }
  .dot-mark {
    width: 11px; height: 11px;
    border-radius: 50%;
    background: var(--red);
    flex: none;
  }

  /* Brand name lockup */
  .brand-name {
    display: flex;
    align-items: center;
    gap: 10px;
    color: var(--red);
    font-weight: 700;
    font-size: 17px;
    line-height: 1.2;
    text-transform: uppercase;
  }
  .brand-name__mark {
    width: 30px; height: 30px;
    border-radius: 50%;
    background: var(--red);
    flex: none;
  }

  /* Services side */
  .card--services {
    display: flex;
    flex-direction: column;
    align-items: center;
    padding-top: 28px;
  }
  .card--services .brand-name { font-size: 19px; }
  .guarantee-badge {
    margin-top: 16px;
    width: 54px; height: 54px;
    border-radius: 50%;
    background: radial-gradient(circle, var(--badge-gold) 0 55%, var(--badge-blue) 56% 100%);
  }
  .services {
    list-style: none;
    margin-top: 20px;
    display: flex;
    flex-wrap: wrap;
    justify-content: center;
    gap: 5px 16px;
    width: 470px;
    font-size: 13.5px;
  }
  .services li { display: flex; align-items: center; gap: 7px; }
  .services li::before {
    content: "";
    width: 8px; height: 8px;
    border-radius: 50%;
    background: var(--red);
  }
  .free-quotes {
    margin-top: 12px;
    color: var(--red);
    font-weight: 700;
    font-size: 14px;
    text-transform: uppercase;
  }
</style>
</head>
<body>

  <section class="card card--contact" aria-label="Contact side">
    <div class="brand-panel">
      <div class="brand-name">
        <span class="brand-name__mark"></span>
        <span>T&amp;K's Pressure Cleaning &amp; Concrete Sealing</span>
      </div>
    </div>
    <div class="divider"></div>
    <div class="contact-panel">
      <div class="person">
        <p class="person-name">Maya</p>
        <p class="contact-line">
          <svg width="11" height="11" viewBox="0 0 24 24" aria-hidden="true"><path fill="#e0201f" d="M6.6 10.8a15.1 15.1 0 0 0 6.6 6.6l2.2-2.2a1 1 0 0 1 1-.25 11.4 11.4 0 0 0 3.6.57 1 1 0 0 1 1 1V20a1 1 0 0 1-1 1A17 17 0 0 1 3 4a1 1 0 0 1 1-1h3.5a1 1 0 0 1 1 1c0 1.25.2 2.45.57 3.57a1 1 0 0 1-.25 1z"/></svg>
          <span>0492 615 370</span>
        </p>
        <p class="contact-line">
          <svg width="11" height="9" viewBox="0 0 24 18" aria-hidden="true"><rect width="24" height="18" rx="2" fill="#e0201f"/><path d="M2 2l10 8 10-8" stroke="#fff" stroke-width="2" fill="none"/></svg>
          <span>maya@tkwashandseal.com</span>
        </p>
      </div>
      <div class="person">
        <p class="person-name">Dylan</p>
        <p class="contact-line">
          <svg width="11" height="11" viewBox="0 0 24 24" aria-hidden="true"><path fill="#e0201f" d="M6.6 10.8a15.1 15.1 0 0 0 6.6 6.6l2.2-2.2a1 1 0 0 1 1-.25 11.4 11.4 0 0 0 3.6.57 1 1 0 0 1 1 1V20a1 1 0 0 1-1 1A17 17 0 0 1 3 4a1 1 0 0 1 1-1h3.5a1 1 0 0 1 1 1c0 1.25.2 2.45.57 3.57a1 1 0 0 1-.25 1z"/></svg>
          <span>0431 528 906</span>
        </p>
        <p class="contact-line">
          <svg width="11" height="9" viewBox="0 0 24 18" aria-hidden="true"><rect width="24" height="18" rx="2" fill="#e0201f"/><path d="M2 2l10 8 10-8" stroke="#fff" stroke-width="2" fill="none"/></svg>
          <span>dylan@tkwashandseal.com</span>
        </p>
      </div>
      <div class="social">
        <p class="contact-line"><span class="dot-mark"></span><span>tkwashandseal</span></p>
        <p class="contact-line"><span class="dot-mark"></span><span>www.tkwashandseal.net</span></p>
      </div>
    </div>
  </section>

  <section class="card card--services" aria-label="Services side">
    <div class="brand-name">
      <span class="brand-name__mark"></span>
      <span>T&amp;K's Pressure Cleaning<br>&amp; Concrete Sealing</span>
    </div>
    <div class="guarantee-badge" role="img" aria-label="100% customer satisfaction guaranteed seal"></div>
    <ul class="services">
      <li>Hot/Cold Hi-Pressure Cleaning</li>
      <li>Sealing &amp; Re-Sealing</li>
      <li>Roof Cleaning</li>
      <li>Colour Sealing</li>
      <li>Decorative Coatings</li>
      <li>Concrete Honing</li>
    </ul>
    <p class="free-quotes">Free no obligation quotes</p>
  </section>

</body>
</html>
```